App Design - Career Prep Pal

We require an App Design for our new App called 'Hiring Helper'. This app is essentially an assistant to help Users prepare for job interviews, to help them get hired. <br/><br/>Users who download the App can view common Questions and Answers, save their favourite responses and also view common Interview Tips. <br/><br/>The vision for our App is for Users who are preparing for an interview (1 week before, 1 day before, even 1 hour before), are able to download, view and educate themselves on common questions and responses, and then be confident to land the job. <br/><br/>Our team has developed wireframes to help highlight what each screen should do and include. Please see attached document, which also highlights key requirements for the experience. Feel free to add/remove/edit what you see on these wireframes. Our preference is that you use Adobe XD please.<br/><br/>In terms of design guidelines, we want the experience to be simple, intuitive and 'memorable' to help Users to remember the questions/responses when they are in the interview. <br/><br/>The final design should communicate 'neat and clean professionalism'; we like the design of: jobvista net au<br/><br/>Thank you for reading! Good luck !

Target Market(s)

Professional job seekers

Font styles to use
Sans Serif

Colors

Designer to choose colors to be used in the design.

Requirements
Must have
• Please see my PixelGuild_UX file that I have uploaded
Nice to have
• Could you also please include some ideas on how we can incorporate Advertising into the app screens

```html
<!DOCTYPE html>
<html lang="en">
<head>
<meta charset="utf-8">
<title>Hiring Helper – App Screens</title>
<link href="https://fonts.googleapis.com/css2?family=Lato:wght@400;700;900&family=Montserrat:wght@700&display=swap" rel="stylesheet">
<style>
  :root{
    --brand-blue:#4C68F6;
    --brand-blue-deep:#3F58D8;
    --ink:#1E1E2A;
    --muted:#8A8FA3;
    --paper:#FFFFFF;
    --canvas:#FFFFFF;
    --logo-yellow:#F5CF3B;
    --illus-soft:#DCE2F7;
    --illus-mid:#B9C4EE;
  }
  *{box-sizing:border-box;margin:0;padding:0}
  html,body{width:1200px;height:720px;overflow:hidden;background:var(--canvas)}
  body{position:relative;font-family:'Lato',sans-serif;color:var(--ink)}

  .screen{position:absolute;width:266px;height:497px;overflow:hidden;box-shadow:0 6px 18px rgba(40,50,90,.12)}
  .brand-name{font-family:'Lato',sans-serif;font-weight:900;color:var(--logo-yellow);white-space:nowrap;letter-spacing:.2px}

  /* dashboard screen */
  .dashboard{left:84px;top:116px;background:var(--brand-blue)}
  .dashboard .backdrop{position:absolute;inset:0}
  .dashboard .back-link{position:absolute;left:28px;top:32px;font-size:9px;color:#555;display:flex;align-items:center;gap:5px}
  .dashboard .back-link svg{width:5px;height:9px}
  .dashboard .brand-name{position:absolute;left:75px;top:27px;font-size:17px}
  .module-card{position:absolute;left:28px;width:216px;height:114px;background:var(--paper);border-radius:5px;box-shadow:0 3px 8px rgba(20,30,80,.18)}
  .module-card .title{position:absolute;left:18px;top:18px;font-size:12.5px;line-height:18px;color:var(--brand-blue);width:110px}
  .module-card .progress{position:absolute;left:18px;top:79px;width:74px;height:1.5px;background:var(--brand-blue)}
  .module-card .progress-short{width:78px;background:linear-gradient(90deg,var(--brand-blue) 20%,#C9D2FB 20%)}
  .module-card .status{position:absolute;left:18px;top:86px;font-size:10px;color:var(--brand-blue)}
  .module-card .art{position:absolute;right:14px;top:36px;width:100px;height:66px;border-radius:4px;background:linear-gradient(135deg,var(--illus-soft),var(--illus-mid))}
  .card-questions{top:81px}
  .card-portfolio{top:214px}
  .card-tips{top:348px}
  .card-tips .art{top:28px;width:86px;height:74px}

  /* welcome screen */
  .welcome{left:459px;top:67px;width:251px;height:542px;border-radius:30px;background:var(--brand-blue)}
  .welcome .photo{position:absolute;inset:0;background:radial-gradient(ellipse at 45% 40%,#5A72F0 0%,#4C68F6 45%,#4560EE 100%)}
  .welcome .hero-art{position:absolute;left:66px;top:153px;width:114px;height:124px;border-radius:8px;background:linear-gradient(160deg,rgba(245,207,59,.55),rgba(255,255,255,.35) 55%,rgba(240,110,70,.45))}
  .welcome .greeting{position:absolute;left:0;right:0;top:326px;text-align:center;color:#fff;font-size:15px;font-weight:400}
  .welcome .brand-name{position:absolute;left:0;right:0;top:360px;text-align:center;font-size:29px}

  /* category screen */
  .categories{left:823px;top:106px;background:var(--paper)}
  .categories .header-band{position:absolute;left:0;top:0;width:266px;height:210px;background:var(--brand-blue)}
  .categories .back-icon{position:absolute;left:28px;top:35px;width:6px;height:10px}
  .categories .brand-name{position:absolute;left:74px;top:27px;font-size:18px}
  .categories .heading{position:absolute;left:0;right:0;top:72px;text-align:center;color:#fff;font-family:'Montserrat',sans-serif;font-weight:700;font-size:13.5px}
  .search{position:absolute;left:31px;top:112px;width:203px;height:34px;border-radius:17px;background:#fff;display:flex;align-items:center;padding-left:18px;gap:8px;font-size:10px;color:#9AA0B4}
  .search svg{width:12px;height:12px}
  .category-card{position:absolute;width:111px;height:101px;background:#fff;border-radius:5px;box-shadow:0 3px 9px rgba(20,30,80,.16)}
  .category-card .art{position:absolute;left:30px;top:12px;width:52px;height:50px;border-radius:4px;background:linear-gradient(135deg,var(--illus-soft),var(--illus-mid))}
  .category-card .name{position:absolute;left:21px;top:66px;font-size:12px;color:var(--ink)}
  .category-card .count{position:absolute;left:21px;top:84px;font-size:7.5px;color:var(--ink)}
  .cat-behavioural{left:14px;top:171px}
  .cat-motivational{left:145px;top:171px}
  .cat-situational{left:14px;top:300px}
  .cat-technical{left:145px;top:300px}
  .view-all{position:absolute;left:57px;top:442px;width:159px;height:33px;background:var(--brand-blue);color:#fff;font-size:12.5px;display:flex;align-items:center;justify-content:center;box-shadow:0 3px 6px rgba(40,60,180,.3)}
</style>
</head>
<body>

<section class="screen dashboard">
  <svg class="backdrop" viewBox="0 0 266 497" preserveAspectRatio="none">
    <path d="M0 0 H193 C178 40 150 68 108 79 C45 98 14 190 0 298 Z" fill="#FFFFFF"/>
  </svg>
  <div class="back-link">
    <svg viewBox="0 0 5 9"><path d="M4.5 0.5 L1 4.5 L4.5 8.5" fill="none" stroke="#4C68F6" stroke-width="1"/></svg>
    Back
  </div>
  <div class="brand-name">Hiring Helper</div>

  <article class="module-card card-questions">
    <div class="title">View Questions &amp; Responses</div>
    <div class="art" role="img" aria-label="Illustration of a person holding a card beside a checklist"></div>
    <div class="progress"></div>
    <div class="status">0% Complete</div>
  </article>

  <article class="module-card card-portfolio">
    <div class="title" style="width:150px">My Question Portfolio</div>
    <div class="art" role="img" aria-label="Illustration of two people beside a screen showing a question mark"></div>
    <div class="progress"></div>
    <div class="status">0% Complete</div>
  </article>

  <article class="module-card card-tips">
    <div class="title">Interview Tips</div>
    <div class="art" role="img" aria-label="Illustration of a person next to a large phone showing a list"></div>
    <div class="progress progress-short"></div>
    <div class="status">20% Complete</div>
  </article>
</section>

<section class="screen welcome">
  <div class="photo" role="img" aria-label="Blue-tinted photo of a job interview in an office"></div>
  <div class="hero-art" role="img" aria-label="Illustration of a microphone with a yellow head"></div>
  <div class="greeting">Welcome to</div>
  <div class="brand-name">Hiring Helper</div>
</section>

<section class="screen categories">
  <div class="header-band"></div>
  <svg class="back-icon" viewBox="0 0 6 10"><path d="M5 0.5 L1 5 L5 9.5" fill="none" stroke="#fff" stroke-width="1.2"/></svg>
  <div class="brand-name">Hiring Helper</div>
  <h2 class="heading">Select your question category</h2>
  <div class="search">
    <svg viewBox="0 0 12 12"><circle cx="5" cy="5" r="4" fill="none" stroke="#9AA0B4" stroke-width="1"/><path d="M8 8 L11.5 11.5" stroke="#9AA0B4" stroke-width="1"/></svg>
    Search here
  </div>

  <article class="category-card cat-behavioural">
    <div class="art" role="img" aria-label="Illustration of a person beside a tall phone"></div>
    <div class="name">Behavioural</div>
    <div class="count">19 Tips</div>
  </article>
  <article class="category-card cat-motivational">
    <div class="art" role="img" aria-label="Illustration of a person arranging tiles"></div>
    <div class="name">Motivational</div>
    <div class="count">24Tips</div>
  </article>
  <article class="category-card cat-situational">
    <div class="art" role="img" aria-label="Illustration of a person beside a tall device"></div>
    <div class="name">Situational</div>
    <div class="count">17 Tips</div>
  </article>
  <article class="category-card cat-technical">
    <div class="art" role="img" aria-label="Illustration of a person working on a laptop"></div>
    <div class="name">Techical</div>
    <div class="count">30 Tips</div>
  </article>

  <div class="view-all">View all</div>
</section>

</body>
</html>
```